BRISKEL Need a luxury modern business card designed.

Need a luxury modern business card designed. refer to the uploaded files for the company name and logo in the zip file under source files. i will making my descion on monday. so please send in before then so if we need to edit we will have the time. we have a trade show coming up and im on a deadline for printer.

Target Market(s)

high end clients

Contact Information for Business Card

Company nAme and logo. Tobias Fennick Co-Founder / Project Manager Office # 555-318-7094 Cell # 555-642-1586 BRISKEL.CA Tobias@briskel-example.ca

Font styles to use
Other font styles liked:
• Modern

Requirements
Must have
• Company name and logo, contact info, using the black, gold and white color scheme.

```html
<!DOCTYPE html>
<html lang="en">
<head>
<meta charset="utf-8">
<title>BRISKEL Business Card</title>
<link rel="stylesheet" href="https://fonts.googleapis.com/css2?family=Lato:wght@300;400;700&family=Open+Sans:wght@400&display=swap">
<style>
  :root {
    --backdrop: #c9c9c9;
    --card-white: #ffffff;
    --card-dark: #2f2f2f;
    --ink: #2a2a2a;
    --gold: #a69563;
    --gold-soft: #d9d0b4;
    --rule-grey: #8a8a8a;
    --soft-white: #f2f2f2;
  }
  * { margin: 0; padding: 0; box-sizing: border-box; }
  html, body { width: 1200px; height: 802px; overflow: hidden; }
  body {
    background: var(--backdrop);
    font-family: "Lato", sans-serif;
    position: relative;
  }
  .card {
    position: absolute;
    top: 274px;
    width: 443px;
    height: 264px;
    overflow: hidden;
    box-shadow: 0 3px 6px rgba(0,0,0,0.25);
  }
  .card-front { left: 136px; background: var(--card-white); }
  .card-back { left: 624px; background: var(--card-dark); }

  .wordmark {
    position: absolute;
    font-family: "Lato", sans-serif;
    font-weight: 300;
    font-size: 32px;
    letter-spacing: 12px;
    line-height: 1;
    white-space: nowrap;
  }
  .tagline {
    position: absolute;
    display: flex;
    align-items: center;
    gap: 6px;
    font-size: 7.5px;
    letter-spacing: 3px;
    font-weight: 700;
    white-space: nowrap;
  }
  .tagline::before, .tagline::after {
    content: "";
    height: 1px;
    flex: 1;
    background: currentColor;
  }

  .card-front .wordmark { left: 24px; top: 42px; color: var(--ink); }
  .card-front .tagline { left: 22px; top: 77px; width: 208px; color: var(--rule-grey); }

  .brand-decoration {
    position: absolute;
    left: 232px;
    top: 0;
    width: 211px;
    height: 264px;
    background: linear-gradient(135deg, var(--gold-soft) 0%, #e9e4d6 55%, #cfcfcf 100%);
  }

  .holder { position: absolute; left: 24px; top: 124px; }
  .holder-name {
    color: var(--gold);
    font-weight: 700;
    font-size: 16.5px;
  }
  .holder-role {
    font-family: "Open Sans", sans-serif;
    color: var(--ink);
    font-size: 11.5px;
    line-height: 16px;
    margin-top: 0;
  }

  .contacts {
    position: absolute;
    left: 24px;
    top: 189px;
    list-style: none;
    color: var(--ink);
    font-family: "Open Sans", sans-serif;
    font-size: 11.5px;
  }
  .contacts li { display: flex; align-items: center; gap: 5px; height: 16px; }
  .contacts svg { width: 11px; height: 11px; flex: none; }

  .back-mark {
    position: absolute;
    left: 207px;
    top: 86px;
    width: 28px;
    height: 28px;
    border: 3px solid var(--gold);
  }
  .card-back .wordmark {
    left: 0; right: 0; top: 153px;
    text-align: center;
    color: var(--soft-white);
    padding-left: 12px;
  }
  .card-back .tagline {
    left: 122px; top: 191px; width: 199px;
    color: var(--soft-white);
  }
</style>
</head>
<body>
  <section class="card card-front" aria-label="Business card front">
    <div class="wordmark">BRISKEL</div>
    <div class="tagline">LUXURY LANDSCAPES</div>

    <div class="brand-decoration" role="img" aria-label="Large gold and black angular brand decoration"></div>

    <div class="holder">
      <div class="holder-name">TOBIAS FENNICK</div>
      <div class="holder-role">Co-Founder<br>Project Manager</div>
    </div>

    <ul class="contacts">
      <li>
        <svg viewBox="0 0 10 10" aria-hidden="true"><path fill="var(--gold)" d="M1 3 Q5 0 9 3 L8 4.5 L6.5 3.8 L6.5 3 Q5 2.5 3.5 3 L3.5 3.8 L2 4.5 Z M2.5 5 H7.5 L8.5 9 H1.5 Z"/></svg>
        555-318-7094
      </li>
      <li>
        <svg viewBox="0 0 10 10" aria-hidden="true"><rect x="2.5" y="0.5" width="5" height="9" rx="1" fill="none" stroke="var(--gold)" stroke-width="1"/><rect x="4.3" y="7.5" width="1.4" height="0.8" fill="var(--gold)"/></svg>
        555-642-1586
      </li>
      <li>
        <svg viewBox="0 0 10 10" aria-hidden="true"><rect x="0.5" y="2" width="9" height="6" fill="var(--gold)"/><path d="M0.5 2 L5 5.5 L9.5 2" fill="none" stroke="#fff" stroke-width="0.8"/></svg>
        briskel.ca Tobias@briskel-example.ca
      </li>
    </ul>
  </section>

  <section class="card card-back" aria-label="Business card back">
    <div class="back-mark" aria-hidden="true"></div>
    <div class="wordmark">BRISKEL</div>
    <div class="tagline">LUXURY LANDSCAPES</div>
  </section>
</body>
</html>
```